U.S. Popcorn company needs business cards

We are a popcorn company that manufactures popcorn and sells it to grocery stores worldwide. Our theme is "Americana" and our logo is U.S. route 66 which is the most famous highway in the U.S.

We would like the design to be simple and to use both sides. On the back side we would like to see just the logo and website. The front would be normal details

Target Market(s)

Wholesalers, grocers and distributors

Industry/Entity Type

Manufacture

Contact Information for Business Card

Business name: Prairie Lantern Popcorn
Phone: +1 555 308 4726
Email: Dale@prairielanternpopcorn.com
website: www.prairielanternpopcorn.com
Tag Line: "Fresh off the open road"
Name: Dale Whitcombe
Title: Founder/President

Requirements
Must have
• Either this design should be fun or clean and simple. I will let you show me your thougths.
Nice to have
• Anything that ties in the real Hwy Route 66.
• Colors might need to be red, white and blue incorporated.
Should not have
• Not be too busy.

```html
<!DOCTYPE html>
<html lang="en">
<head>
<meta charset="utf-8">
<title>Prairie Lantern Popcorn – Business Cards</title>
<link rel="stylesheet" href="https://fonts.googleapis.com/css2?family=Source+Sans+3:ital,wght@0,400;0,700;1,600&display=swap">
<style>
  :root {
    --ground: #5b4a3b;
    --navy: #062466;
    --red: #e3232c;
    --white: #ffffff;
    --card-shadow: rgba(0, 0, 0, 0.35);
  }
  * { margin: 0; padding: 0; box-sizing: border-box; }
  html, body {
    width: 1200px;
    height: 987px;
    overflow: hidden;
  }
  body {
    background: var(--ground);
    font-family: "Source Sans 3", sans-serif;
    position: relative;
  }
  .card {
    position: absolute;
    left: 293px;
    width: 615px;
    height: 351px;
    background: var(--white);
    box-shadow: 0 2px 6px var(--card-shadow);
    overflow: hidden;
  }
  .card--front { top: 130px; }
  .card--back { top: 505px; }

  .front-panel {
    position: absolute;
    inset: 0;
    width: 100%;
    height: 100%;
  }
  .front-panel polygon { fill: var(--navy); }

  .wordmark {
    position: absolute;
    font-weight: 700;
    line-height: 1.02;
    text-transform: uppercase;
    text-align: center;
    letter-spacing: 0.5px;
  }
  .card--front .wordmark {
    right: 22px;
    top: 92px;
    width: 190px;
    font-size: 38px;
    color: var(--red);
  }
  .card--back .wordmark {
    left: 0;
    right: 0;
    top: 92px;
    font-size: 40px;
    color: var(--navy);
  }

  .contact {
    position: absolute;
    left: 30px;
    top: 200px;
    color: var(--white);
  }
  .contact__name {
    font-size: 22px;
    font-weight: 400;
    color: var(--red);
    line-height: 1.1;
  }
  .contact__title {
    font-size: 17px;
    line-height: 1.3;
    margin-bottom: 12px;
  }
  .contact__list { list-style: none; }
  .contact__item {
    display: flex;
    align-items: center;
    gap: 10px;
    font-size: 15px;
    height: 23.5px;
  }
  .contact__icon {
    width: 13px;
    height: 13px;
    flex: none;
  }
  .contact__icon .icon-fill { fill: var(--red); }
  .contact__icon .icon-line { fill: none; stroke: var(--red); stroke-width: 1.4; }

  .tagline {
    position: absolute;
    left: 0;
    right: 0;
    top: 296px;
    text-align: center;
    font-size: 18px;
    font-style: italic;
    font-weight: 600;
    color: var(--navy);
  }
</style>
</head>
<body>

  <section class="card card--front" aria-label="Business card front">
    <svg class="front-panel" viewBox="0 0 615 351" preserveAspectRatio="none" aria-hidden="true">
      <polygon points="0,0 380,0 350,351 0,351"/>
    </svg>

    <div class="wordmark">Prairie<br>Lantern<br>Popcorn</div>

    <div class="contact">
      <p class="contact__name">Dale Whitcombe</p>
      <p class="contact__title">Founder/President</p>
      <ul class="contact__list">
        <li class="contact__item">
          <svg class="contact__icon" viewBox="0 0 16 16" aria-hidden="true">
            <path class="icon-fill" d="M3.6 1.2l2.3 2.6c.4.4.4 1 0 1.4L4.8 6.4c.9 2 2.6 3.7 4.6 4.6l1.2-1.1c.4-.4 1-.4 1.4 0l2.6 2.3c.4.4.4 1 0 1.4l-1.4 1.4c-.6.6-1.5.8-2.3.5C6.2 14 2 9.8.5 5.2c-.3-.8-.1-1.7.5-2.3L2.2 1.2c.4-.4 1-.4 1.4 0z"/>
          </svg>
          <span>+1 555 308 4726</span>
        </li>
        <li class="contact__item">
          <svg class="contact__icon" viewBox="0 0 16 16" aria-hidden="true">
            <path class="icon-fill" d="M1 3h14v1.2L8 9 1 4.2z"/>
            <path class="icon-fill" d="M1 5.8l7 4.8 7-4.8V13H1z"/>
          </svg>
          <span>Dale@prairielanternpopcorn.com</span>
        </li>
        <li class="contact__item">
          <svg class="contact__icon" viewBox="0 0 16 16" aria-hidden="true">
            <circle class="icon-line" cx="8" cy="8" r="6.5"/>
            <ellipse class="icon-line" cx="8" cy="8" rx="2.8" ry="6.5"/>
            <path class="icon-line" d="M1.5 8h13"/>
          </svg>
          <span>www.prairielanternpopcorn.com</span>
        </li>
      </ul>
    </div>
  </section>

  <section class="card card--back" aria-label="Business card back">
    <div class="wordmark">Prairie<br>Lantern<br>Popcorn</div>
    <p class="tagline">Fresh off the open road</p>
  </section>

</body>
</html>
```